Software Development Consulting Company Needs Business Card Design

We need a new business card design for our consultants at Kestrel Works (kestrelworks.example). We are a small firm that provides high-end software development and methodology consulting to medium to large enterprise IT organizations.

Our logo uses Futura for the font and we would like to stick with navy blue and canary yellow for the logo colors. Attached are normal and reversed versions of our logos in illustrator format.
Updates

Hi Everyone, Thank yo very much for your amazing design ideas. I have created a poll for this project and our employees will be voting on the design they wish to use. We will be making a decision this Wednesday (October 22nd). Thanks again, Dale Hartwick

Industry/Entity Type

Business

```html
<!DOCTYPE html>
<html lang="en">
<head>
<meta charset="utf-8">
<title>Kestrel Works — Business Card</title>
<link rel="stylesheet" href="https://fonts.googleapis.com/css2?family=Jost:wght@500&family=Open+Sans:wght@400;700&display=swap">
<style>
  :root {
    --navy: #1c3f66;
    --canary: #fff200;
    --paper: #ffffff;
    --ink: #4a4a4a;
    --backdrop: #e9eaee;
    --globe: #6b7c8f;
  }
  * { box-sizing: border-box; margin: 0; padding: 0; }
  html, body { width: 1200px; height: 980px; overflow: hidden; }
  body {
    background: var(--backdrop);
    position: relative;
    font-family: "Open Sans", Arial, sans-serif;
  }
  .card {
    position: absolute;
    width: 560px;
    height: 320px;
    border-radius: 28px;
    box-shadow: 0 10px 28px rgba(0,0,0,0.16);
  }
  .card--back {
    left: 580px; top: 90px;
    background: var(--canary);
    display: flex; flex-direction: column;
    align-items: center; justify-content: center;
    gap: 42px;
  }
  .card--front {
    left: 60px; top: 540px;
    background: var(--paper);
    padding: 52px 56px;
  }
  .wordmark {
    display: flex; align-items: center; gap: 14px;
  }
  .wordmark__dot {
    width: 16px; height: 16px; border-radius: 50%;
    background: var(--navy);
  }
  .wordmark__name {
    font-family: "Jost", "Futura", sans-serif;
    font-weight: 500;
    font-size: 44px;
    letter-spacing: 6px;
    text-transform: uppercase;
    color: var(--navy);
    line-height: 1;
  }
  .card--front .wordmark { justify-content: flex-end; }
  .card--front .wordmark__name { font-size: 38px; }
  .site-url {
    font-size: 20px;
    letter-spacing: 3px;
    color: var(--ink);
  }
  .holder {
    margin-top: 34px;
    text-align: right;
    font-size: 20px;
    color: var(--navy);
  }
  .holder__name { font-weight: 700; }
  .holder__title { color: var(--ink); font-size: 17px; }
  .contact {
    list-style: none;
    margin-top: 22px;
    display: grid;
    grid-template-columns: auto auto;
    gap: 8px 26px;
    font-size: 16px;
    color: var(--ink);
  }
  .contact__item { display: flex; align-items: center; gap: 8px; }
  .contact__item--wide { grid-column: 1 / -1; }
  .contact svg { width: 15px; height: 15px; flex: none; }
</style>
</head>
<body>
  <section class="card card--back" aria-label="Card back">
    <div class="wordmark">
      <span class="wordmark__dot"></span>
      <span class="wordmark__name">Kestrel Works</span>
    </div>
    <p class="site-url">www.kestrelworks.example</p>
  </section>

  <section class="card card--front" aria-label="Card front">
    <div class="wordmark">
      <span class="wordmark__dot"></span>
      <span class="wordmark__name">Kestrel Works</span>
    </div>
    <p class="holder"><span class="holder__name">Your Name,</span> <span class="holder__title">Title</span></p>
    <ul class="contact">
      <li class="contact__item">
        <svg viewBox="0 0 16 16" aria-hidden="true"><circle cx="8" cy="8" r="7" fill="none" stroke="#4a4a4a" stroke-width="1.4"/><path d="M5.5 4.5l1.5 1.5-1 1a5 5 0 0 0 3 3l1-1 1.5 1.5-1.2 1.2C7.8 11.7 4.3 8.2 4.3 5.7z" fill="#4a4a4a"/></svg>
        555-014-2783
      </li>
      <li class="contact__item">
        <svg viewBox="0 0 16 16" aria-hidden="true"><rect x="1.5" y="3.5" width="13" height="9" rx="1" fill="none" stroke="#1c3f66" stroke-width="1.5"/><path d="M1.5 4l6.5 5 6.5-5" fill="none" stroke="#1c3f66" stroke-width="1.5"/></svg>
        info@kestrelworks.example
      </li>
      <li class="contact__item contact__item--wide">
        <svg viewBox="0 0 16 16" aria-hidden="true"><circle cx="8" cy="8" r="6.5" fill="none" stroke="#6b7c8f" stroke-width="1.3"/><ellipse cx="8" cy="8" rx="3" ry="6.5" fill="none" stroke="#6b7c8f" stroke-width="1.1"/><path d="M1.5 8h13M2.6 4.8h10.8M2.6 11.2h10.8" stroke="#6b7c8f" stroke-width="1"/></svg>
        www.kestrelworks.example
      </li>
      <li class="contact__item contact__item--wide">Riverton + Oakfield, IL</li>
    </ul>
  </section>
</body>
</html>
```